Business card design for a dynamic IT consulting company

We need a business card design for a young firm, specialized in the Telecommunications/Consulting industry. The name of the company is Quindor and Partners Business Consulting Ltd. (Short name: Quindor and Partnes)
Quindor = solve read reverse, so we aim to be uncomplicated and solution-oriented. The small pipe in our logo is also related to the word solve. So we need a new business card design, which is simple, eye catching and something non traditional (I would probably prefer a square shaped design rather than a rectangle, but open for suggestions). Attached our logo.

Target Market(s)

Usually our customers are Tier1 Telecoms providers (Q-Netra, Palorix, etc) and their executives.

Industry/Entity Type

Business

Contact Information for Business Card

Name: Bence Tolnavari
Email: b.tolnavari@quindor.hu
Web: www.quindor.hu
Mobile: +36 30 518 2769
Title: Managing Director

Optional:
Company name: Quindor and Partners Ltd.
Address: 1087 Budapest, Tolvenka str. 28/C, Hungary

Font styles to use
Other font styles liked:
• helveticaneue_medium, Prime Regular are used now.

Colors

Designer to choose colors to be used in the design.

Requirements
Must have
• I would like to have a 2 sided design.
Nice to have
• I thought if we make the logo a bit bigger (without the company name), that could go to the back with the company name below. I though, if the pipe in the logo is somehow touchable on the business card, would be nice and unique.

```html
<!DOCTYPE html>
<html lang="en">
<head>
<meta charset="utf-8">
<title>Quindor and Partners – Business Card</title>
<link rel="stylesheet" href="https://fonts.googleapis.com/css2?family=Oswald:wght@500&family=Work+Sans:wght@400;500&family=Saira:wght@500&display=swap">
<style>
  :root {
    --bg: #1b1b1d;
    --card-white: #ffffff;
    --brand-blue: #1a8fd6;
    --brand-magenta: #b9318f;
    --text-gray: #555a60;
    --text-white: #ffffff;
  }
  * { margin: 0; padding: 0; box-sizing: border-box; }
  html, body { width: 1200px; height: 897px; overflow: hidden; background: var(--bg); }
  .stage { position: relative; width: 1200px; height: 897px; }

  .card { position: absolute; left: 303px; width: 595px; height: 338px; overflow: hidden; }
  .card-front { top: 92px; background: var(--card-white); }
  .card-back { top: 469px; background: var(--brand-magenta); }

  .front-glow {
    position: absolute; right: -40px; top: -60px; width: 300px; height: 300px; border-radius: 50%;
    background: radial-gradient(circle, rgba(0,0,0,0.025) 0%, rgba(0,0,0,0.015) 55%, rgba(0,0,0,0) 70%);
  }

  .person { position: absolute; right: 304px; top: 138px; text-align: right; }
  .person-name {
    font-family: 'Oswald', sans-serif; font-weight: 500; font-size: 31px; line-height: 34px;
    color: var(--brand-blue); letter-spacing: 0.5px; text-transform: uppercase;
  }
  .person-title {
    font-family: 'Work Sans', sans-serif; font-size: 14px; line-height: 18px;
    color: var(--text-gray); letter-spacing: 0.6px; margin-top: 2px; text-transform: uppercase;
  }
  .divider { position: absolute; left: 314px; top: 141px; width: 2px; height: 55px; background: var(--brand-magenta); }

  .contacts { position: absolute; left: 342px; top: 141px; list-style: none; }
  .contacts li {
    display: flex; align-items: center; height: 19.5px;
    font-family: 'Work Sans', sans-serif; font-size: 13.5px; color: var(--text-gray);
  }
  .contacts svg { width: 11px; height: 11px; margin-right: 7px; fill: var(--brand-blue); flex: none; }

  .company { position: absolute; left: 0; right: 0; top: 275px; text-align: center; }
  .company-name {
    font-family: 'Saira', sans-serif; font-weight: 500; font-size: 14.5px; line-height: 18px;
    color: var(--brand-blue); text-transform: uppercase;
  }
  .company-address { font-family: 'Work Sans', sans-serif; font-size: 13px; line-height: 17px; color: var(--text-gray); letter-spacing: 0.3px; }

  .brand-name {
    position: absolute; left: 0; right: 0; top: 136px; text-align: center;
    font-family: 'Work Sans', sans-serif; font-weight: 500; font-size: 46px; line-height: 60px;
    color: var(--text-white);
  }
  .back-web {
    position: absolute; left: 0; right: 0; top: 294px; text-align: center;
    font-family: 'Work Sans', sans-serif; font-size: 15px; letter-spacing: 2px; color: var(--text-white);
  }
</style>
</head>
<body>
<main class="stage">
  <section class="card card-front">
    <div class="front-glow"></div>
    <div class="person">
      <h1 class="person-name">Bence Tolnavari</h1>
      <p class="person-title">Managing Director</p>
    </div>
    <div class="divider"></div>
    <ul class="contacts">
      <li><svg viewBox="0 0 24 24"><path d="M6.6 10.8a15.1 15.1 0 0 0 6.6 6.6l2.2-2.2c.3-.3.7-.4 1-.2 1.1.4 2.3.6 3.6.6.6 0 1 .4 1 1V20c0 .6-.4 1-1 1A17 17 0 0 1 3 4c0-.6.4-1 1-1h3.5c.6 0 1 .4 1 1 0 1.3.2 2.5.6 3.6.1.3 0 .7-.2 1z"/></svg>+36 30 518 2769</li>
      <li><svg viewBox="0 0 24 24"><path d="M2 5h20v14H2z M2 5l10 8 10-8" fill="none" stroke="#1a8fd6" stroke-width="0"/><path d="M2 5h20l-10 8z M2 7l10 8 10-8v12H2z"/></svg>b.tolnavari@quindor.hu</li>
      <li><svg viewBox="0 0 24 24"><g fill="none" stroke="#1a8fd6" stroke-width="2"><circle cx="12" cy="12" r="9"/><ellipse cx="12" cy="12" rx="4" ry="9"/><path d="M3 12h18M5 7h14M5 17h14"/></g></svg>www.quindor.hu</li>
    </ul>
    <div class="company">
      <p class="company-name">Quindor and Partners Ltd:</p>
      <p class="company-address">1087 Budapest, Tolvenka str. 28/C, Hungary</p>
    </div>
  </section>

  <section class="card card-back">
    <p class="brand-name">Quindor &amp; Partners</p>
    <p class="back-web">www.quindor.hu</p>
  </section>
</main>
</body>
</html>
```